Brell Stone Company Business Cards

Front and Back Business Card - logo and text setup - cool design. I need workable photoshop or illustrator files so I can setup each employee card with design that is created
Updates

Hi everyone, thank you for the great entries. Please no more white and blue cards - there are so many already - black and silver only now please. thanks!

Target Market(s)

Construction Industry - Facility Managers

Industry/Entity Type

Construction

Contact Information for Business Card

I really like contemporary simplistic looks - clean neat....not opposed to seeing some black backrounds

Requirements
Must have
• Logo/website address with design on front only - www.brellstone-example.com (logo attached)
• Back:
• Name/Title/Company Address/Phone/email address
Nice to have
• Cool design
Should not have
• Nothing gimmicky like Fire or Water - since we are a Fire Protection company - it has all been done

```html
<!DOCTYPE html>
<html lang="en">
<head>
<meta charset="utf-8">
<title>Brell Stone Company – Business Cards</title>
<link rel="stylesheet" href="https://fonts.googleapis.com/css2?family=Open+Sans:wght@400;600;800&display=swap">
<style>
  :root {
    --backdrop: #1b1b1c;
    --card-top: #3a3a3c;
    --card-bottom: #232325;
    --card-edge: #4a4a4d;
    --silver: #c9cacc;
    --silver-dark: #8e8f92;
    --text-light: #f2f2f2;
  }
  * { margin: 0; padding: 0; box-sizing: border-box; }
  html, body {
    width: 1200px;
    height: 874px;
    overflow: hidden;
    background: var(--backdrop);
    font-family: "Open Sans", Arial, sans-serif;
  }
  .stage {
    width: 1200px;
    height: 874px;
    display: flex;
    flex-direction: column;
    align-items: center;
    justify-content: center;
    gap: 34px;
  }
  .card {
    width: 640px;
    height: 366px;
    border-radius: 22px;
    background: linear-gradient(160deg, var(--card-top) 0%, var(--card-bottom) 100%);
    box-shadow: 0 0 0 1px var(--card-edge) inset, 0 12px 30px rgba(0,0,0,0.55);
    position: relative;
    display: flex;
    align-items: center;
    justify-content: center;
  }
  .card-front .brand-name {
    font-weight: 800;
    font-size: 58px;
    letter-spacing: -1px;
    color: var(--silver);
    text-align: center;
    line-height: 1.1;
  }
  .card-back .contact {
    text-align: center;
    color: var(--text-light);
  }
  .contact .person {
    font-size: 22px;
    font-weight: 600;
    margin-bottom: 6px;
  }
  .contact .person .role {
    font-size: 16px;
    font-weight: 400;
  }
  .contact .line {
    font-size: 14px;
    line-height: 1.55;
  }
  .contact .website {
    font-size: 14px;
    letter-spacing: 4px;
    margin-top: 2px;
  }
</style>
</head>
<body>
  <main class="stage">
    <section class="card card-front" aria-label="Card front">
      <div class="brand-name">Brell Stone<br>Company</div>
    </section>
    <section class="card card-back" aria-label="Card back">
      <div class="contact">
        <p class="person">Alan Merrow <span class="role">- CEO/Founder</span></p>
        <p class="line">48 Harbor Park Road, Milbrook, NY 11900</p>
        <p class="line">P. (555) 014-2288 F. (555) 014-2290 E. info@brellstone-example.com</p>
        <p class="website">www.brellstone-example.com</p>
      </div>
    </section>
  </main>
</body>
</html>
```